Business Card for Fashion House

We need a business card design for our personalize fashion service for our customers. the business card should reflect reliability, luxury and creativity.
The brand Gravetto is extracted from "Graceful Velvetto"; Gravetto provides fashion designs sprinkled with luxury and style tailored for our elite clients character profile.
Gravetto is created for those who embody class and elegance with a passion for style.
Target Market(s)
Affluent Customers
Industry/Entity Type
Fashion
Contact Information for Business Card
Samira Haddadin
Fashion Designer
Telephone: +971 4 555 0192
Mobile +971 50 555 0147
Emal info@gravetto-example.com
Website www.gravetto-example.com
Social Media Youtube g+ Facebook Instagram Pin /gravetto
Font styles to use
Other font styles liked:
- Audrey provided
Look and feel
Each slider illustrates characteristics of the customer's brand and the style your logo design should communicate.

```html
<!DOCTYPE html>
<html lang="en">
<head>
<meta charset="utf-8">
<title>Gravetto — Business Card</title>
<link rel="stylesheet" href="https://fonts.googleapis.com/css2?family=Marcellus&family=Roboto:wght@400&display=swap">
<style>
  :root {
    --backdrop: #d8d3cd;
    --card: #eceeef;
    --card-edge: #f7f8f8;
    --ink: #2b2b2d;
    --ink-soft: #3a3a3c;
  }
  * { box-sizing: border-box; margin: 0; padding: 0; }
  html, body {
    width: 1200px;
    height: 1054px;
    overflow: hidden;
    background: var(--backdrop);
  }
  .business-card {
    position: absolute;
    left: 100px;
    top: 224px;
    width: 1000px;
    height: 606px;
    background: var(--card);
    border: 1px solid var(--card-edge);
    color: var(--ink);
    font-family: "Roboto", Arial, sans-serif;
  }
  .holder-name {
    position: absolute;
    left: 51px;
    top: 58px;
    font-family: "Marcellus", Georgia, serif;
    font-size: 40px;
    font-weight: 400;
    letter-spacing: 0.5px;
    color: var(--ink);
  }
  .holder-role {
    position: absolute;
    left: 51px;
    top: 114px;
    font-size: 20px;
    color: var(--ink-soft);
  }
  .brand-mark {
    position: absolute;
    right: 62px;
    top: 110px;
    display: flex;
    align-items: center;
    gap: 14px;
  }
  .brand-mark__dot {
    width: 22px;
    height: 22px;
    border-radius: 50%;
    background: var(--ink);
  }
  .brand-mark__name {
    font-family: "Marcellus", Georgia, serif;
    font-size: 44px;
    color: var(--ink);
    letter-spacing: 1px;
  }
  .contact-list {
    position: absolute;
    left: 51px;
    top: 424px;
    list-style: none;
  }
  .contact-list__item {
    display: flex;
    align-items: center;
    height: 34px;
    font-size: 24px;
    color: var(--ink);
  }
  .contact-list__icon {
    width: 24px;
    height: 24px;
    margin-right: 21px;
    flex: none;
  }
  .social-handle {
    position: absolute;
    right: 64px;
    top: 526px;
    display: flex;
    align-items: center;
    gap: 10px;
    font-size: 25px;
    color: var(--ink);
  }
  .social-handle__dot {
    width: 22px;
    height: 22px;
    border-radius: 50%;
    background: var(--ink);
  }
</style>
</head>
<body>
  <main class="business-card">
    <h1 class="holder-name">Samira Haddadin</h1>
    <p class="holder-role">Fashion Designer</p>

    <div class="brand-mark">
      <span class="brand-mark__dot"></span>
      <span class="brand-mark__name">Gravetto</span>
    </div>

    <ul class="contact-list">
      <li class="contact-list__item">
        <svg class="contact-list__icon" viewBox="0 0 24 24" fill="none" stroke="currentColor" stroke-width="1.8" aria-hidden="true">
          <circle cx="12" cy="12" r="10"/>
          <path d="M8.5 7.5c.6-.6 1.3-.5 1.7.1l.9 1.5c.3.5.2 1-.2 1.4l-.6.5c.5 1.2 1.5 2.2 2.7 2.7l.5-.6c.4-.4.9-.5 1.4-.2l1.5.9c.6.4.7 1.1.1 1.7-.8.9-2 1.1-3.1.6-2.4-1-4.3-2.9-5.3-5.3-.5-1.1-.3-2.3.4-3.3z" fill="currentColor" stroke="none"/>
        </svg>
        +971 4 555 0192
      </li>
      <li class="contact-list__item">
        <svg class="contact-list__icon" viewBox="0 0 24 24" fill="none" stroke="currentColor" stroke-width="1.8" aria-hidden="true">
          <rect x="6" y="2" width="12" height="20" rx="2"/>
          <line x1="10" y1="18.5" x2="14" y2="18.5"/>
        </svg>
        +971 50 555 0147
      </li>
      <li class="contact-list__item">
        <svg class="contact-list__icon" viewBox="0 0 24 24" fill="none" stroke="currentColor" stroke-width="1.8" aria-hidden="true">
          <rect x="2" y="5" width="20" height="14" rx="1"/>
          <path d="M2.5 5.5l9.5 7.5 9.5-7.5"/>
        </svg>
        info@gravetto-example.com
      </li>
      <li class="contact-list__item">
        <svg class="contact-list__icon" viewBox="0 0 24 24" fill="none" stroke="currentColor" stroke-width="1.6" aria-hidden="true">
          <circle cx="12" cy="12" r="10"/>
          <ellipse cx="12" cy="12" rx="4.5" ry="10"/>
          <line x1="2" y1="12" x2="22" y2="12"/>
          <path d="M4 7h16M4 17h16"/>
        </svg>
        www.gravetto-example.com
      </li>
    </ul>

    <div class="social-handle">
      <span class="social-handle__dot"></span>
      <span>/gravetto</span>
    </div>
  </main>
</body>
</html>
```